Hi Morvina, we need our wine labels produced for this year's vintage with a few changes. We would like to keep the integrity of the current label for the H and want the blue and gold to remain in the design. However we would like to include an image of a tree and our dogs.

```html
<!DOCTYPE html>
<html lang="en">
<head>
<meta charset="utf-8">
<title>Corbelle Estate – Ashby's Paddock Pinot Noir Label</title>
<link rel="stylesheet" href="https://fonts.googleapis.com/css2?family=Arimo:wght@400;700&family=Cormorant+Garamond:ital,wght@1,500&display=swap">
<style>
  :root {
    --navy: #1c1b5f;
    --gold: #7d6526;
    --gold-light: #b39a57;
    --ink: #111111;
    --paper: #ffffff;
    --backdrop: #eceeef;
  }
  html, body {
    margin: 0;
    padding: 0;
    overflow: hidden;
  }
  body {
    width: 1200px;
    height: 923px;
    background: var(--backdrop);
    position: relative;
    font-family: "Arimo", Arial, sans-serif;
  }
  .wine-label {
    position: absolute;
    left: 250px;
    top: 141px;
    width: 700px;
    height: 640px;
    background: var(--paper);
    overflow: hidden;
  }
  .top-band {
    position: absolute;
    left: 0;
    top: 0;
    width: 700px;
    height: 110px;
  }
  .brand-mark-name {
    position: absolute;
    left: 0;
    width: 700px;
    top: 94px;
    text-align: center;
    font-weight: 700;
    font-size: 11px;
    letter-spacing: 1px;
    color: var(--gold);
  }
  .estate-name {
    position: absolute;
    left: 0;
    width: 700px;
    top: 114px;
    margin: 0;
    text-align: center;
    font-weight: 700;
    font-size: 46px;
    line-height: 1;
    color: var(--gold);
  }
  .vineyard-name {
    position: absolute;
    left: 0;
    width: 700px;
    top: 160px;
    margin: 0;
    text-align: center;
    font-family: "Cormorant Garamond", Georgia, serif;
    font-style: italic;
    font-weight: 500;
    font-size: 50px;
    line-height: 1;
    color: var(--navy);
  }
  .tree-illustration {
    position: absolute;
    left: 208px;
    top: 210px;
    width: 272px;
    height: 309px;
    background: radial-gradient(ellipse at 50% 40%, var(--gold-light) 0%, #d9ccaa 60%, var(--paper) 100%);
  }
  .variety, .vintage, .region {
    position: absolute;
    left: 0;
    width: 700px;
    text-align: center;
    font-weight: 700;
    color: var(--ink);
    line-height: 1;
    margin: 0;
  }
  .variety { top: 528px; font-size: 26px; }
  .vintage { top: 555px; font-size: 26px; }
  .region { top: 587px; font-size: 19px; }
  .legal {
    position: absolute;
    font-size: 14px;
    color: var(--ink);
    line-height: 1;
  }
  .preservative { left: 11px; top: 590px; }
  .volume { right: 11px; top: 567px; text-align: right; }
  .abv { right: 11px; top: 589px; text-align: right; }
  .bottom-band {
    position: absolute;
    left: 0;
    top: 607px;
    width: 700px;
    height: 33px;
  }
</style>
</head>
<body>
  <main class="wine-label">
    <svg class="top-band" viewBox="0 0 700 110" width="700" height="110">
      <rect role="img" aria-label="Navy chevron pattern band" x="0" y="0" width="700" height="90" fill="var(--navy)"/>
      <rect role="img" aria-label="Gold chevron pattern strip" x="0" y="88" width="700" height="22" fill="var(--gold)"/>
      <circle cx="351" cy="110" r="69" fill="var(--paper)"/>
      <rect x="336" y="58" width="30" height="30" fill="var(--gold)"/>
    </svg>
    <div class="brand-mark-name">CORBELLE</div>

    <h1 class="estate-name">CORBELLE ESTATE</h1>
    <h2 class="vineyard-name">Ashby's Paddock</h2>

    <div class="tree-illustration" role="img" aria-label="Gold line drawing of a tall tree with two small dogs sitting at its base"></div>

    <p class="variety">PINOT NOIR</p>
    <p class="vintage">2019</p>
    <p class="region">YARROWDALE VALLEY</p>

    <span class="legal preservative">Preservative 220 added</span>
    <span class="legal volume">750 ml</span>
    <span class="legal abv">ALC/VOL 14.8%</span>

    <svg class="bottom-band" viewBox="0 0 700 33" width="700" height="33">
      <rect role="img" aria-label="Gold chevron pattern band" x="0" y="0" width="700" height="33" fill="var(--gold)"/>
    </svg>
  </main>
</body>
</html>
```